English and Spanish Language School Needs a Business Card

Need a business card design a startup company called Maribel Language School. The company will offer English and Spanish conversational level courses designed to make the learner feel comfortable with grammar and vocabulary. We would like to see a logo with some colour that should communicate learning, growth.

Target Market(s)

Consumers and businesses

Industry/Entity Type

Education

Contact Information for Business Card

TBD

Font styles to use
Serif

Requirements
Must have
• Include the following
• Logo
• Name
• Title
• Cellphone Number
• Office Phone number
• Email address
• Office Address

```html
<!DOCTYPE html>
<html lang="en">
<head>
<meta charset="utf-8">
<title>Maribel Language School – Business Card</title>
<link href="https://fonts.googleapis.com/css2?family=Montserrat:wght@400;500;600;700&display=swap" rel="stylesheet">
<style>
  :root {
    --backdrop: #2a2a2b;
    --card: #050505;
    --red: #d3262d;
    --teal: #16a4b2;
  }
  * { box-sizing: border-box; margin: 0; padding: 0; }
  html, body { width: 1200px; height: 900px; overflow: hidden; }
  body {
    background: var(--backdrop);
    font-family: "Montserrat", Arial, sans-serif;
    display: flex;
    flex-direction: column;
    align-items: center;
    justify-content: center;
    gap: 36px;
  }
  .card {
    position: relative;
    width: 700px;
    height: 400px;
    background: var(--card);
    border-radius: 24px;
  }
  .brand {
    display: flex;
    align-items: center;
    gap: 14px;
    color: var(--red);
    font-weight: 700;
    line-height: 1;
  }
  .brand-dot {
    width: 22px; height: 22px;
    border-radius: 50%;
    background: var(--teal);
    flex-shrink: 0;
  }
  .brand-name { display: flex; flex-direction: column; }
  .brand-name .main { font-size: 64px; letter-spacing: -1px; }
  .brand-name .sub { font-size: 28px; margin-top: 6px; }

  .card--front .brand { position: absolute; left: 175px; top: 120px; }
  .website {
    position: absolute;
    left: 0; right: 0; bottom: 46px;
    text-align: center;
    font-size: 19px;
    font-weight: 500;
    color: var(--teal);
    letter-spacing: 0.3px;
  }
  .website .accent { color: var(--red); }

  .card--back .brand { position: absolute; left: 44px; top: 140px; }
  .card--back .brand-name .main { font-size: 50px; }
  .card--back .brand-name .sub { font-size: 22px; }

  .contact {
    position: absolute;
    left: 400px; top: 118px;
    color: var(--teal);
    font-size: 16px;
    line-height: 1.35;
  }
  .contact .person { color: var(--red); font-size: 24px; font-weight: 700; letter-spacing: 0.5px; }
  .contact .role { margin-bottom: 4px; }
  .contact .address { margin-bottom: 12px; }
  .contact ul { list-style: none; }
  .contact li { display: flex; align-items: center; gap: 10px; }
  .contact li svg { width: 13px; height: 13px; flex-shrink: 0; }
  .contact .web { color: var(--red); font-weight: 700; }
</style>
</head>
<body>
  <section class="card card--front">
    <div class="brand">
      <span class="brand-dot"></span>
      <div class="brand-name">
        <span class="main">Maribel</span>
        <span class="sub">Language School</span>
      </div>
    </div>
    <p class="website"><span class="accent">www.</span>maribellanguageschool<span class="accent">.com</span></p>
  </section>

  <section class="card card--back">
    <div class="brand">
      <span class="brand-dot"></span>
      <div class="brand-name">
        <span class="main">Maribel</span>
        <span class="sub">Language School</span>
      </div>
    </div>
    <div class="contact">
      <p class="person">Daniel Harper</p>
      <p class="role">Director</p>
      <p class="address">Po Box 218<br>Ashford VIC 3122</p>
      <ul>
        <li>
          <svg viewBox="0 0 14 14" fill="none" stroke="#d3262d" stroke-width="1.6"><rect x="3.5" y="1" width="7" height="12" rx="1.5"/><line x1="6" y1="11" x2="8" y2="11"/></svg>
          +330 2418-5520
        </li>
        <li>
          <svg viewBox="0 0 14 14" fill="#d3262d"><path d="M3 1l2.5 3-1.3 1.6c.8 1.8 2.2 3.2 4 4l1.6-1.3 3 2.5-1.5 2.2C6 12.5 1.5 8 0.8 2.5z"/></svg>
          +330 2471-3309
        </li>
        <li>
          <svg viewBox="0 0 14 14" fill="none" stroke="#d3262d" stroke-width="1.5"><rect x="1" y="3" width="12" height="8" rx="1"/><path d="M1 3.5l6 4.5 6-4.5"/></svg>
          hello@maribelschool.com
        </li>
        <li>
          <svg viewBox="0 0 14 14" fill="none" stroke="#d3262d" stroke-width="1.3"><circle cx="7" cy="7" r="6"/><ellipse cx="7" cy="7" rx="2.6" ry="6"/><line x1="1" y1="7" x2="13" y2="7"/></svg>
          <span class="web">maribellanguageschool.com</span>
        </li>
      </ul>
    </div>
  </section>
</body>
</html>
```